Business Card Design for Marketing Firm

Looking for business card design for higher end marketing firm. Clean but impressionable/trendy. We are a marketing firm that represents manufacturers in the foodservice equipment and supply industry. Our customers are end users such has hotels, restaurants, country clubs, convention centers and casinos as well as distributors of restaurants supplies and equipment, and manufacturers of foodservice equipment and supplies.
Target Market(s)
Hotels, Restaurants, Supply & Equipment Distributors, Foodservice Manufacturers
Industry/Entity Type
Foodservice/Hospitality
Contact Information for Business Card
Name, Title, Contact Number, Email, Website, Social Media, Address
Requirements
Must have
- Clean & Simple but Serious and Impressionable

```html
<!DOCTYPE html>
<html lang="en">
<head>
<meta charset="utf-8">
<title>Meridian Service Reps – Business Card</title>
<link href="https://fonts.googleapis.com/css2?family=EB+Garamond:wght@400;600&display=swap" rel="stylesheet">
<style>
  :root {
    --backdrop: #2a2a2c;
    --card: #f7f7f8;
    --card-shade: #e9e9ec;
    --navy: #27267a;
    --ink: #4a4a52;
    --rule: #7b7ab0;
  }
  * { box-sizing: border-box; margin: 0; padding: 0; }
  html, body {
    width: 1200px; height: 900px; overflow: hidden;
    background: var(--backdrop);
    font-family: "EB Garamond", Georgia, serif;
  }
  .stage { position: relative; width: 1200px; height: 900px; }

  .card {
    position: absolute;
    width: 620px; height: 354px;
    background: linear-gradient(135deg, var(--card) 0%, #ffffff 45%, var(--card-shade) 100%);
    overflow: hidden;
    box-shadow: 0 18px 40px rgba(0,0,0,.45);
  }
  .card--front { left: 120px; top: 60px; }
  .card--back  { left: 460px; top: 486px; }

  .brand-mark {
    position: absolute;
    right: -90px; top: 30px;
    width: 330px; height: 330px;
    border-radius: 50%;
    background: var(--navy);
  }

  .wordmark {
    position: absolute;
    color: var(--navy);
    font-weight: 400;
    text-transform: uppercase;
    letter-spacing: 1px;
  }
  .wordmark__name { display: block; font-size: 30px; line-height: 1; }
  .wordmark__sub { display: block; text-align: right; font-size: 15px; letter-spacing: 2px; margin-top: 2px; }
  .wordmark__rule { display: block; height: 1.5px; background: var(--navy); margin-top: 4px; }

  .card--front .wordmark { left: 48px; top: 110px; width: 330px; }

  .social {
    position: absolute; left: 150px; top: 190px;
    display: flex; gap: 14px;
  }
  .social__dot { width: 30px; height: 30px; border-radius: 50%; background: var(--navy); opacity: .85; }

  .card--back .wordmark { left: 44px; top: 60px; width: 290px; }
  .card--back .wordmark__name { font-size: 26px; }
  .card--back .wordmark__sub { font-size: 13px; }

  .person { position: absolute; left: 44px; top: 152px; }
  .person__name { color: var(--navy); font-weight: 600; font-size: 22px; letter-spacing: 1px; text-transform: uppercase; }
  .person__title { color: var(--ink); font-size: 16px; }

  .contact { position: absolute; left: 44px; top: 212px; list-style: none; width: 380px; }
  .contact__item { display: flex; align-items: center; gap: 10px; color: var(--ink); font-size: 16px; line-height: 25px; }
  .contact__item svg { width: 14px; height: 14px; flex: none; fill: none; stroke: var(--navy); stroke-width: 1.6; }
  .contact__rule { height: 1px; background: var(--rule); margin: 8px 0 6px; }
  .contact__city { color: var(--ink); font-size: 17px; }
</style>
</head>
<body>
<main class="stage">

  <section class="card card--front" aria-label="Card front">
    <div class="wordmark">
      <span class="wordmark__name">Meridian Service</span>
      <span class="wordmark__sub">Reps</span>
      <span class="wordmark__rule"></span>
    </div>
    <div class="social" aria-label="Social media">
      <span class="social__dot"></span>
      <span class="social__dot"></span>
      <span class="social__dot"></span>
    </div>
    <div class="brand-mark" aria-hidden="true"></div>
  </section>

  <section class="card card--back" aria-label="Card back">
    <div class="wordmark">
      <span class="wordmark__name">Meridian Service</span>
      <span class="wordmark__sub">Reps</span>
      <span class="wordmark__rule"></span>
    </div>
    <div class="person">
      <p class="person__name">Dana Whitfield</p>
      <p class="person__title">Director</p>
    </div>
    <ul class="contact">
      <li class="contact__item">
        <svg viewBox="0 0 16 16"><path d="M4 1.5l2.5 3-1.6 1.6a9 9 0 0 0 5 5l1.6-1.6 3 2.5-1.8 2.3C7.5 14 2 8.5 1.7 3.3z"/></svg>
        555-0142-7700
      </li>
      <li class="contact__item">
        <svg viewBox="0 0 16 16"><rect x="1.5" y="3.5" width="13" height="9"/><path d="M1.5 3.5L8 9l6.5-5.5"/></svg>
        info@meridianservicereps.com
      </li>
      <li class="contact__item">
        <svg viewBox="0 0 16 16"><circle cx="8" cy="8" r="6.5"/><path d="M1.5 8h13M8 1.5c-3 3.5-3 9.5 0 13M8 1.5c3 3.5 3 9.5 0 13"/></svg>
        www.meridianservicereps.com
      </li>
      <li class="contact__rule" aria-hidden="true"></li>
      <li class="contact__city">Cedar Bend, Texas</li>
    </ul>
    <div class="brand-mark" aria-hidden="true"></div>
  </section>

</main>
</body>
</html>
```